HearthMile business card and stationary design

We are looking for a simple yet elegant design for our mortgage company business card and stationary.

The card should include:
Name (Marcus Pell)
Title (CEO)
Phone Number (732-555-0182)
Address (48 Birchwell Court, Suite 314, Larkmoor, NJ 08214)
Email (email@hearthmile.example)
"NMLS" i.e. (NMLS 61947)
"Company NMLS" (Company NMLS 274615)

Contact Information for Business Card

See above

```html
<!DOCTYPE html>
<html lang="en">
<head>
<meta charset="utf-8">
<title>HearthMile Business Card</title>
<link rel="stylesheet" href="https://fonts.googleapis.com/css2?family=Montserrat:wght@400;500;700&display=swap">
<style>
  :root {
    --card: #1b1b1c;
    --page: #2a2a2c;
    --blue: #1ea3e0;
    --white: #f4f4f4;
    --muted: #d8d8d8;
    --emboss: #4a4a4d;
  }
  * { box-sizing: border-box; margin: 0; padding: 0; }
  html, body { width: 1200px; height: 900px; overflow: hidden; }
  body {
    background: var(--page);
    font-family: "Montserrat", sans-serif;
    display: flex;
    flex-direction: column;
    align-items: center;
    justify-content: center;
    gap: 40px;
  }
  .card {
    position: relative;
    width: 700px;
    height: 400px;
    background: var(--card);
    border-bottom: 9px solid var(--blue);
    box-shadow: 0 14px 30px rgba(0,0,0,.45);
    overflow: hidden;
  }
  .brand-name {
    font-weight: 500;
    color: var(--white);
    letter-spacing: .5px;
    display: flex;
    align-items: center;
    gap: 12px;
    white-space: nowrap;
  }
  .brand-mark {
    width: 14px; height: 14px;
    background: var(--blue);
  }
  .card-front .brand-name {
    position: absolute;
    left: 56px; top: 118px;
    font-size: 46px;
  }
  .divider {
    position: absolute;
    left: 372px; top: 100px;
    width: 1.5px; height: 190px;
    background: var(--blue);
  }
  .contact {
    position: absolute;
    left: 398px; top: 104px;
    color: var(--white);
    font-size: 14px;
    line-height: 1.45;
    white-space: nowrap;
  }
  .contact-name {
    color: var(--blue);
    font-weight: 700;
    font-size: 20px;
    letter-spacing: 1px;
    text-transform: uppercase;
  }
  .contact-title { margin-bottom: 8px; }
  .contact-address { margin-bottom: 10px; }
  .contact-line { display: flex; align-items: center; gap: 8px; }
  .contact-line svg { width: 12px; height: 12px; flex: none; }
  .licence {
    position: absolute;
    left: 56px; bottom: 36px;
    color: var(--muted);
    font-size: 13px;
    letter-spacing: .4px;
  }
  .licence .dot { color: var(--blue); margin: 0 6px; }
  .card-back {
    display: flex;
    align-items: center;
    justify-content: center;
  }
  .card-back .brand-name {
    font-size: 72px;
    color: var(--emboss);
  }
  .card-back .brand-mark { background: var(--emboss); width: 20px; height: 20px; }
</style>
</head>
<body>
  <section class="card card-front">
    <div class="brand-name"><span class="brand-mark"></span>HearthMile</div>
    <div class="divider"></div>
    <div class="contact">
      <div class="contact-name">Marcus Pell</div>
      <div class="contact-title">CEO</div>
      <div class="contact-address">48 Birchwell Court, Suite 314<br>Larkmoor, NJ 08214</div>
      <div class="contact-line">
        <svg viewBox="0 0 12 12" aria-hidden="true"><path d="M2.5 1h2l1 2.5-1.3 1a6 6 0 0 0 3.3 3.3l1-1.3L11 7.5v2A1.5 1.5 0 0 1 9.5 11 8.5 8.5 0 0 1 1 2.5 1.5 1.5 0 0 1 2.5 1z" fill="var(--blue)"/></svg>
        732-555-0182
      </div>
      <div class="contact-line">
        <svg viewBox="0 0 12 12" aria-hidden="true"><rect x="0.5" y="2" width="11" height="8" fill="var(--blue)"/><path d="M0.5 2.5 6 6.5l5.5-4" stroke="var(--card)" fill="none" stroke-width="1"/></svg>
        email@hearthmile.example
      </div>
      <div class="contact-line">
        <svg viewBox="0 0 12 12" aria-hidden="true"><circle cx="6" cy="6" r="5.5" fill="var(--blue)"/><path d="M0.5 6h11M6 .5c-2.5 3-2.5 8 0 11M6 .5c2.5 3 2.5 8 0 11" stroke="var(--card)" fill="none" stroke-width=".8"/></svg>
        www.hearthmile.example
      </div>
    </div>
    <div class="licence">NMLS 61947<span class="dot">•</span>Company NMLS 274615</div>
  </section>

  <section class="card card-back">
    <div class="brand-name"><span class="brand-mark"></span>HearthMile</div>
  </section>
</body>
</html>
```